Detail Shop Business card design

i need a business card design for my new detailing company called 'Brisk's Polish Works'. i want an all black and white design . simple, direct and to the point. i want the designer to choose a fitting font to match the logothe front should have logo, address, phone and email and the back side should have a slogan and text indicating that we offer services on anything including cars, trucks, motorcycles and RVs. slogan will read "we take pride in your ride"
maybe also very small on the back side the IG icon with Brisks_Polish_Works

phone 208.417.6352
address 3847 E Larkin Ave
Spokane WA 99214
email: BrisksPolish@mailvexo.com

Target Market(s)

all ages , auto enthusiasts

Industry/Entity Type

Automotive

Contact Information for Business Card

the front should have logo, address, phone and email and the back side should have a slogan and text indicating that we offer services on anything including cars, trucks, motorcycles and RVs. slogan will read "we take pride in your ride"

phone 208.417.6352
address 3847 E Larkin Ave
Spokane WA 99214

Colors
000000
ffffff

Requirements
Must have
• bold font and very simple design with good spacing
Nice to have
• anything creative from the designer indicating we service any types of vehicles
Should not have
• any colors ,

```html
<!DOCTYPE html>
<html lang="en">
<head>
<meta charset="utf-8">
<title>Brisk's Polish Works – Business Card</title>
<link rel="stylesheet" href="https://fonts.googleapis.com/css2?family=Roboto:wght@400;500;700&family=Roboto+Condensed:wght@400&display=swap">
<style>
  :root {
    --ink: #000000;
    --paper: #ffffff;
    --backdrop: #e4e4e4;
    --card-edge: #d0d0d0;
  }
  * { box-sizing: border-box; margin: 0; padding: 0; }
  html, body { width: 1200px; height: 960px; overflow: hidden; }
  body {
    position: relative;
    background: var(--backdrop);
    font-family: "Roboto", Arial, sans-serif;
    color: var(--ink);
  }
  .card {
    position: absolute;
    background: var(--paper);
    border: 1px solid var(--card-edge);
    overflow: hidden;
  }
  .card--front { left: 315px; top: 113px; width: 598px; height: 342px; }
  .card--back  { left: 311px; top: 473px; width: 600px; height: 342px; }

  .brand {
    position: absolute;
    left: 0; right: 0;
    display: flex;
    align-items: center;
    justify-content: center;
    gap: 12px;
    font-weight: 700;
    color: var(--ink);
    letter-spacing: 0.02em;
  }
  .brand__dot { border-radius: 50%; background: var(--ink); flex: none; }
  .card--front .brand { top: 88px; font-size: 30px; }
  .card--front .brand__dot { width: 20px; height: 20px; }
  .card--back .brand { top: 112px; font-size: 42px; }
  .card--back .brand__dot { width: 28px; height: 28px; }

  .ribbon { position: absolute; left: 0; top: 0; width: 598px; height: 342px; }

  .holder {
    position: absolute;
    right: 358px;
    top: 232px;
    text-align: right;
    color: var(--paper);
  }
  .holder__name { font-size: 19px; font-weight: 500; line-height: 22px; }
  .holder__role { font-size: 15px; line-height: 20px; margin-bottom: 6px; }
  .holder__address { font-size: 14px; line-height: 20px; font-style: normal; }

  .contacts {
    position: absolute;
    left: 355px;
    top: 238px;
    list-style: none;
    color: var(--paper);
    font-size: 14px;
    line-height: 19.5px;
  }
  .contacts li { display: flex; align-items: center; gap: 9px; }
  .contacts svg { width: 11px; height: 11px; flex: none; fill: var(--paper); }

  .slogan {
    position: absolute;
    left: 0; right: 0;
    top: 270px;
    text-align: center;
    font-size: 17px;
    font-weight: 700;
    letter-spacing: 0.01em;
  }
  .slogan-rule {
    position: absolute;
    left: 141px;
    width: 321px;
    top: 292px;
    height: 1.5px;
    background: var(--ink);
  }
  .services {
    position: absolute;
    left: 0; right: 0;
    top: 297px;
    text-align: center;
    font-family: "Roboto Condensed", "Arial Narrow", sans-serif;
    font-size: 13px;
  }
</style>
</head>
<body>

<section class="card card--front" aria-label="Card front">
  <div class="brand"><span class="brand__dot"></span><span>BRISK'S POLISH WORKS</span></div>

  <svg class="ribbon" viewBox="0 0 598 342" aria-hidden="true">
    <polygon points="3,220 265,220 265,330 3,330 33,275" fill="var(--ink)"/>
    <polyline points="10,225 261,225" stroke="var(--paper)" stroke-width="1" fill="none"/>
    <polyline points="10,325 261,325" stroke="var(--paper)" stroke-width="1" fill="none"/>
    <rect x="265" y="238" width="61" height="80" fill="var(--ink)"/>
    <line x1="265" y1="243" x2="326" y2="243" stroke="var(--paper)" stroke-width="1"/>
    <line x1="265" y1="313" x2="326" y2="313" stroke="var(--paper)" stroke-width="1"/>
    <circle cx="295.5" cy="278" r="18" fill="var(--paper)"/>
    <polygon points="326,220 597,220 570,275 597,330 326,330" fill="var(--ink)"/>
    <polyline points="330,225 588,225" stroke="var(--paper)" stroke-width="1" fill="none"/>
    <polyline points="330,325 588,325" stroke="var(--paper)" stroke-width="1" fill="none"/>
  </svg>

  <div class="holder">
    <p class="holder__name">DANE HOLLOWAY</p>
    <p class="holder__role">CEO/FOUNDER</p>
    <address class="holder__address">3847 E Larkin Ave<br>Spokane WA 99214</address>
  </div>

  <ul class="contacts">
    <li><svg viewBox="0 0 12 12"><path d="M2.4 0.5 4.3 2.6 3.4 4.2C4.1 5.8 5.9 7.6 7.8 8.6L9.4 7.7 11.5 9.6 10.2 11.5C5.6 11.3 0.7 6.4 0.5 1.8Z"/></svg>208.417.6352</li>
    <li><svg viewBox="0 0 12 12"><path d="M3 0h6v12H3zM4 1.2v8.3h4V1.2zM5.4 10.2h1.2v1H5.4z" fill-rule="evenodd"/></svg>208 552 7190</li>
    <li><svg viewBox="0 0 12 12"><path d="M0 2.5h12v7H0zM0.6 2.8 6 6.8 11.4 2.8" /><path d="M0.6 2.8 6 6.8 11.4 2.8" stroke="var(--ink)" stroke-width="1" fill="none"/></svg>BrisksPolish@mailvexo.com</li>
    <li><svg viewBox="0 0 12 12"><circle cx="6" cy="6" r="5.5"/><path d="M6 0.5v11M0.5 6h11M6 0.5C3.5 3 3.5 9 6 11.5M6 0.5C8.5 3 8.5 9 6 11.5" stroke="var(--ink)" stroke-width="0.8" fill="none"/></svg>www.briskspolish.com</li>
  </ul>
</section>

<section class="card card--back" aria-label="Card back">
  <div class="brand"><span class="brand__dot"></span><span>BRISK'S POLISH WORKS</span></div>
  <p class="slogan">WE TAKE PRIDE IN YOUR RIDE</p>
  <div class="slogan-rule"></div>
  <p class="services">we offer services on anything including cars, trucks, motorcycles &amp; RVs</p>
</section>

</body>
</html>
```